Animal Eye Clinic needs a Business card

We are a new veterinary ophthalmology practice (Ridgeline Pet Vision Care) and we need a business card designed. We only see animal eyes - we are not a regular veterinary clinic. We already have a logo. We are looking for a professional, good looking business card to hand out to our clients. We are looking for something simple but professional and contemporary. Our logo is likely the only picture/graphic that needs to be on the card.
Updates

Contact Information for Business Card

Delia Vossman, BSc, DVM, MSc, DipACVO
Veterinary Ophthalmologist

Phone: 250.418.3927
Email: ridgelinepetvisioncare@mailbox-example.net
Website: ridgelinepetvisioncare-example.net
Address: 1874 Thornbury Rd
Kelowna, BC, V1X 4M9

Colors

Designer to choose colors to be used in the design.

Requirements
Must have
• Our logo (attached)

```html
<!DOCTYPE html>
<html lang="en">
<head>
<meta charset="utf-8">
<title>Ridgeline Pet Vision Care – Business Card</title>
<link rel="stylesheet" href="https://fonts.googleapis.com/css2?family=Lato:wght@400;700&display=swap">
<style>
  :root {
    --page-bg: #2b2c2e;
    --card-bg: #1d1e20;
    --card-edge: #26272a;
    --teal: #1a9aa8;
    --text-light: #f1f2f3;
    --text-grey: #8d9094;
    --rule: #6c6f73;
    --pattern-a: #222326;
    --pattern-b: #1b1c1e;
  }
  * { box-sizing: border-box; margin: 0; padding: 0; }
  html, body {
    width: 1200px; height: 1108px; overflow: hidden;
    background: var(--page-bg);
    font-family: "Lato", Arial, sans-serif;
  }
  .stage {
    position: relative; width: 1200px; height: 1108px;
    display: flex; justify-content: center; align-items: center; gap: 80px;
  }
  .card {
    position: relative; width: 400px; height: 700px;
    background: var(--card-bg); border-radius: 24px;
    box-shadow: 0 18px 40px rgba(0,0,0,.45), inset 0 0 0 1px var(--card-edge);
    overflow: hidden;
  }
  /* Front */
  .card-front { display: flex; flex-direction: column; align-items: center; text-align: center; }
  .brand { margin-top: 120px; display: flex; align-items: center; gap: 14px; }
  .brand-dot { width: 44px; height: 44px; border-radius: 50%; background: var(--teal); flex: none; }
  .brand-name {
    color: var(--teal); font-weight: 700; font-size: 25px; line-height: 1.15;
    text-align: left; text-transform: uppercase; letter-spacing: .5px;
  }
  .person { margin-top: 140px; }
  .person-name { color: var(--teal); font-weight: 700; font-size: 22px; text-transform: uppercase; letter-spacing: .5px; }
  .person-credentials { color: var(--text-grey); font-size: 15px; margin-top: 4px; }
  .person-title { color: var(--text-light); font-size: 16px; margin-top: 4px; }
  .icon-row { display: flex; align-items: center; gap: 8px; margin-top: 16px; width: 310px; }
  .icon-row .rule { flex: 1; height: 1px; background: var(--rule); }
  .icon { width: 24px; height: 24px; border-radius: 50%; background: var(--teal); display: flex; align-items: center; justify-content: center; }
  .icon svg { width: 14px; height: 14px; fill: var(--card-bg); }
  .contact { margin-top: 14px; color: var(--text-light); font-size: 15.5px; line-height: 1.45; }
  .contact .phone { font-size: 18px; }
  .divider { width: 240px; height: 1px; background: var(--rule); margin: 14px 0; }
  .address { color: var(--text-light); font-size: 17px; line-height: 1.4; }
  /* Back */
  .pattern-field {
    position: absolute; inset: 0;
    background: linear-gradient(160deg, var(--pattern-a) 0%, var(--pattern-b) 75%);
  }
  .back-mark {
    position: absolute; left: 0; right: 0; top: 470px;
    display: flex; justify-content: center;
  }
  .back-name { color: var(--teal); font-weight: 700; font-size: 16px; text-transform: uppercase; letter-spacing: .5px; }
</style>
</head>
<body>
<main class="stage">
  <section class="card card-front" aria-label="Card front">
    <div class="brand">
      <span class="brand-dot"></span>
      <div class="brand-name">Ridgeline Pet<br>Vision Care</div>
    </div>
    <div class="person">
      <div class="person-name">Delia Vossman</div>
      <div class="person-credentials">BSC, DVM, MSC, DIPACVO</div>
      <div class="person-title">Veterinary Ophthalmologist</div>
    </div>
    <div class="icon-row">
      <span class="rule"></span>
      <span class="icon"><svg viewBox="0 0 24 24"><path d="M6.6 10.8a15 15 0 0 0 6.6 6.6l2.2-2.2a1 1 0 0 1 1-.25 11.4 11.4 0 0 0 3.6.57 1 1 0 0 1 1 1V20a1 1 0 0 1-1 1A17 17 0 0 1 3 4a1 1 0 0 1 1-1h3.5a1 1 0 0 1 1 1c0 1.25.2 2.45.57 3.57a1 1 0 0 1-.25 1z"/></svg></span>
      <span class="icon"><svg viewBox="0 0 24 24"><path d="M3 5h18v14H3z M3 5l9 7 9-7" fill="none" stroke="#1d1e20" stroke-width="2.2"/></svg></span>
      <span class="icon"><svg viewBox="0 0 24 24"><path d="M12 2a7 7 0 0 0-7 7c0 5.2 7 13 7 13s7-7.8 7-13a7 7 0 0 0-7-7zm0 9.5A2.5 2.5 0 1 1 12 6.5a2.5 2.5 0 0 1 0 5z"/></svg></span>
      <span class="rule"></span>
    </div>
    <div class="contact">
      <div class="phone">250.418.3927</div>
      <div>ridgelinepetvisioncare@mailbox-example.net</div>
      <div>www.ridgelinepetvisioncare-example.net</div>
    </div>
    <div class="divider"></div>
    <div class="address">1874 Thornbury Rd<br>Kelowna, BC, V1X 4M9</div>
  </section>

  <section class="card card-back" aria-label="Card back">
    <div class="pattern-field" role="img" aria-label="Faint tone-on-tone repeating pattern of the clinic mark"></div>
    <div class="back-mark"><span class="back-name">Ridgeline Pet Vision Care</span></div>
  </section>
</main>
</body>
</html>
```